folding sales brochure

We need a brochure in the colors of orange, black and charcoal gray - our logo colors.
www.vennotraduxpartners

Strong, clean - and something eye catching.

We are looking for graphic images and photos that depict international business, written translation, live simultaneous interpretation for conferences & events with people communicating. We have some photos, but are open to others.

This brochure will generalize our companies services.
This brochure will be used for B2B as well as Trade Show booths.
Updates

Reason: Project has been extended to allow time for feedback and completion. Thank you all... some wonderful designs.

Thank you all for your designs - they were all creative in so many different ways, making the choice of just one very difficult.

regards,
Delia

Target Market(s)

Our target is large global corporate companies.

Industry/Entity Type

Events

Requirements
Must have
• company logo (will supply)
company website and address etc.

Our Type Font is: Helvetica Neue LT Std

All info needed can be found here: www.vennotraduxpartners
Should not have
• we feel globes and flags are overdone in the International marketplace - hopefully you can find something else to speak Global.

```html
<!DOCTYPE html>
<html lang="en">
<head>
<meta charset="utf-8">
<title>Venno Tradux Partners – Folder Brochure</title>
<link href="https://fonts.googleapis.com/css2?family=Arimo:wght@400;700&display=swap" rel="stylesheet">
<style>
  :root {
    --orange: #f28c28;
    --orange-light: #f7a654;
    --orange-deep: #e27d1c;
    --charcoal: #5a5b5e;
    --band-gray: #646569;
    --ink: #333333;
    --label-gray: #b4b4b4;
    --rule: #555555;
    --paper: #ffffff;
    --paper-edge: #dcdcdc;
  }
  * { margin: 0; padding: 0; box-sizing: border-box; }
  html, body { width: 1200px; height: 898px; overflow: hidden; background: #fff; }
  body { font-family: "Arimo", "Helvetica Neue", Arial, sans-serif; }

  .sheet {
    position: relative; width: 1200px; height: 898px;
    border: 1px solid var(--rule); background: #fff;
  }
  .sheet-label { position: absolute; color: var(--label-gray); font-size: 22px; }
  .sheet-label--back { left: 300px; top: 6px; }
  .sheet-label--front { left: 852px; top: 10px; }
  .sheet-label--size { left: 536px; top: 868px; }

  .spread {
    position: absolute; left: 17px; top: 36px; width: 1166px; height: 826px;
    border: 1px solid var(--rule); overflow: hidden;
  }
  .page {
    position: absolute; top: 0; width: 583px; height: 100%;
    background: radial-gradient(ellipse 70% 45% at 50% 36%, var(--paper) 40%, var(--paper-edge) 100%);
  }
  .page--back { left: 0; }
  .page--front {
    left: 583px; border-left: 1px solid var(--rule);
    background: radial-gradient(ellipse 80% 40% at 50% 20%, var(--paper) 40%, var(--paper-edge) 100%);
  }

  .band-gray { position: absolute; left: 0; top: 521px; width: 100%; height: 14px; background: var(--band-gray); }
  .band-orange { position: absolute; left: 0; top: 535px; width: 100%; height: 77px; background: var(--orange); }
  .band-orange svg { position: absolute; inset: 0; }
  .band-url {
    position: absolute; top: 35px; width: 100%; text-align: center;
    color: #fff; font-size: 15.5px; letter-spacing: 0.2px;
  }

  .brand { position: absolute; display: flex; align-items: center; white-space: nowrap; }
  .brand-dot { flex: none; border-radius: 50%; background: var(--orange); }
  .brand-name { color: var(--charcoal); font-weight: 700; letter-spacing: -0.5px; }

  .brand--front { left: 172px; top: 98px; gap: 10px; }
  .brand--front .brand-dot { width: 36px; height: 36px; }
  .brand--front .brand-name { font-size: 30px; }

  .brand--back { left: 66px; top: 748px; gap: 7px; }
  .brand--back .brand-dot { width: 26px; height: 26px; }
  .brand--back .brand-name { font-size: 21px; }

  .hero-photo { position: absolute; left: 20px; top: 242px; }

  .headline {
    position: absolute; left: 175px; top: 656px;
    color: var(--orange); font-size: 35px; line-height: 41px; font-weight: 400;
    text-transform: uppercase;
  }

  .contact {
    position: absolute; left: 253px; top: 732px; color: var(--ink);
    font-size: 10.5px; line-height: 12.5px; font-style: normal;
  }
  .contact-name { font-weight: 700; }
  .contact-gap { margin-top: 6px; }
</style>
</head>
<body>
<div class="sheet">
  <span class="sheet-label sheet-label--back">Back</span>
  <span class="sheet-label sheet-label--front">front</span>

  <div class="spread">
    <section class="page page--back">
      <div class="band-gray"></div>
      <div class="band-orange">
        <svg width="583" height="77" viewBox="0 0 583 77" aria-hidden="true">
          <rect x="360" y="0" width="90" height="77" fill="var(--orange-light)" opacity="0.35"/>
          <rect x="395" y="0" width="8" height="77" fill="#fff" opacity="0.15"/>
          <polygon points="450,0 583,0 583,77 530,77" fill="var(--orange-deep)" opacity="0.5"/>
        </svg>
        <p class="band-url">www.vennotraduxpartners.com</p>
      </div>

      <div class="brand brand--back">
        <span class="brand-dot"></span>
        <span class="brand-name">venno tradux</span>
      </div>
      <address class="contact">
        <div class="contact-name">Venno Tradux Partners</div>
        <div>4120 Harbor Crest Way, Suite 210 Lindenvale, CA 90412</div>
        <div>Mailing address: P.O. Box 551207 Lindenvale, CA 90418</div>
        <div class="contact-gap">Phone:+1 555 204 7710 | Toll free:+1 800 555 0142</div>
        <div>Fax:+1 555 204 7719 | Email: info@vennotradux.example</div>
      </address>
    </section>

    <section class="page page--front">
      <div class="brand brand--front">
        <span class="brand-dot"></span>
        <span class="brand-name">venno tradux</span>
      </div>

      <svg class="hero-photo" width="563" height="275" viewBox="0 0 563 275" role="img"
           aria-label="Photo: two business people shaking hands in front of glass office towers">
        <defs>
          <linearGradient id="heroTone" x1="0" y1="0" x2="1" y2="1">
            <stop offset="0" stop-color="#6f9cc9"/>
            <stop offset="0.45" stop-color="#2f5170"/>
            <stop offset="1" stop-color="#14202c"/>
          </linearGradient>
        </defs>
        <polygon points="0,274 292,0 563,0 563,274" fill="url(#heroTone)"/>
      </svg>

      <div class="band-gray"></div>
      <div class="band-orange">
        <svg width="583" height="77" viewBox="0 0 583 77" aria-hidden="true">
          <polygon points="330,14 583,14 583,30 310,30" fill="var(--orange-light)" opacity="0.55"/>
          <polygon points="360,48 583,48 583,60 345,60" fill="var(--orange-light)" opacity="0.4"/>
        </svg>
        <p class="band-url">www.vennotraduxpartners.com</p>
      </div>

      <h1 class="headline">Seamless live<br>multilingual<br>communication</h1>
    </section>
  </div>

  <span class="sheet-label sheet-label--size">Each page A4 size</span>
</div>
</body>
</html>
```